Firm Stationery Design

I need a design for stationery, including: Stationery First Page, Stationery Second Sheet, Envelope, Mailing Label for Flat Envelopes, and Business Cards

```html
<!DOCTYPE html>
<html lang="en">
<head>
<meta charset="utf-8">
<title>Harlow Law LLC – Stationery</title>
<link href="https://fonts.googleapis.com/css2?family=Montserrat:wght@700;800&family=Roboto:wght@300;400;500&display=swap" rel="stylesheet">
<style>
:root{
  --bg:#e8e9eb;
  --paper:#ffffff;
  --ink:#1b1b1c;
  --orange:#f7a01e;
  --bronze:#c27b14;
  --grey-panel:#e4e4e6;
  --text:#3a3a3a;
  --muted:#6a6a6a;
}
*{margin:0;padding:0;box-sizing:border-box}
html,body{width:1200px;height:992px;overflow:hidden;background:var(--bg)}
body{position:relative;font-family:"Roboto",Arial,sans-serif;color:var(--text)}
.piece{position:absolute;background:var(--paper)}
.band{position:absolute;left:0;right:0;bottom:0;background:var(--ink)}
.band::before{content:"";position:absolute;left:0;right:0;top:-3px;height:1.5px;background:var(--orange)}

/* wordmark */
.mark{display:flex;flex-direction:column;align-items:center;gap:4px}
.mark-square{background:var(--orange)}
.mark-name{font-family:"Montserrat",Arial,sans-serif;font-weight:800;color:var(--ink);letter-spacing:.3px;line-height:1;white-space:nowrap}

.contact{font-family:"Roboto",Arial,sans-serif;color:var(--text);line-height:1.4}
.contact .ico{display:inline-block;vertical-align:middle;margin-right:3px}
.person-name{font-family:"Montserrat",Arial,sans-serif;font-weight:700;color:var(--ink)}
.person-role{color:var(--orange)}

/* business card front */
.card-front{left:55px;top:60px;width:315px;height:180px}
.card-front .band{height:12px}
.card-front .mark{position:absolute;left:18px;top:42px;width:112px}
.card-front .mark-square{width:30px;height:30px}
.card-front .mark-name{font-size:13.5px}
.card-front .divider{position:absolute;left:140px;top:40px;width:1px;height:88px;background:var(--ink)}
.card-front .details{position:absolute;left:154px;top:38px}
.card-front .person-name{font-size:12.5px}
.card-front .person-role{font-size:8px;margin-bottom:8px}
.card-front .contact{font-size:8.6px}
.card-front .addr{margin-bottom:6px}

.card-back{left:55px;top:246px;width:315px;height:179px;background:linear-gradient(135deg,#6b6b6b 0%,#2a2a2a 45%,#0d0d0d 100%)}

/* letterhead */
.letter{left:395px;top:60px;width:310px;height:399px}
.letter .band{height:8px}
.letter .mark{position:absolute;left:18px;top:22px;width:92px}
.letter .mark-square{width:20px;height:20px}
.letter .mark-name{font-size:11px}
.letter .head-contact{position:absolute;left:217px;top:25px;font-size:5.4px;line-height:1.35}
.letter .body{position:absolute;left:32px;top:102px;width:248px;font-size:4.6px;line-height:1.45;color:var(--muted)}
.letter .body p{margin-bottom:6px}
.letter .sign{position:absolute;left:32px;top:310px;font-size:4.6px;color:var(--muted);line-height:1.4}
.letter .sign svg{display:block;margin-top:8px}

/* envelope back */
.env-back{left:734px;top:62px;width:410px;height:190px}
.env-back .panel{position:absolute;left:209px;top:0;right:0;bottom:10px;background:var(--grey-panel)}
.env-back .band{height:8px}
.env-back .mark{position:absolute;left:20px;top:38px;width:120px}
.env-back .mark-square{width:24px;height:24px}
.env-back .mark-name{font-size:12.5px}
.env-back .ret{position:absolute;left:20px;top:94px;width:120px;text-align:center;font-size:5.8px}

.env-front{left:734px;top:265px;width:410px;height:195px;background:transparent}
.env-front svg{position:absolute;inset:0}
.env-front .mark{position:absolute;left:150px;top:20px;width:110px}
.env-front .mark-square{width:20px;height:20px}
.env-front .mark-name{font-size:13px;color:var(--paper)}

/* folder cover */
.folder-cover{left:55px;top:490px;width:535px;height:345px}
.folder-cover .spine{position:absolute;left:0;top:0;width:267px;height:100%;background:linear-gradient(180deg,#2e2b28 0%,#1c1c1d 55%,#1b1b1c 100%)}
.folder-cover .back-info{position:absolute;left:0;width:267px;bottom:24px;text-align:center;color:#fff;font-size:6.4px;line-height:1.3}
.folder-cover .mark{position:absolute;left:267px;width:268px;top:100px}
.folder-cover .mark-square{width:44px;height:44px}
.folder-cover .mark-name{font-size:28px}
.folder-cover .web{position:absolute;left:267px;width:268px;bottom:20px;text-align:center;font-size:7px;letter-spacing:1.2px;color:var(--ink)}
.folder-cover .web span{color:var(--orange)}

/* folder inside */
.folder-in{left:612px;top:488px;width:531px;height:346px;background:transparent}
.folder-in .left{position:absolute;left:0;top:0;width:265px;height:100%;background:linear-gradient(90deg,#ffffff 0%,#f3f3f4 60%,#d6d6d8 100%)}
.folder-in .sheet{position:absolute;left:265px;top:0;width:266px;height:100%;background:var(--paper)}
.folder-in .sheet .mark{position:absolute;left:12px;top:16px;width:84px}
.folder-in .sheet .mark-square{width:16px;height:16px}
.folder-in .sheet .mark-name{font-size:10px}
.folder-in .sheet .head-contact{position:absolute;left:185px;top:20px;font-size:4.8px;line-height:1.35}
.folder-in .sheet .body{position:absolute;left:27px;top:87px;width:212px;font-size:3.9px;line-height:1.45;color:var(--muted)}
.folder-in .sheet .body p{margin-bottom:5px}
.folder-in svg.pocket{position:absolute;left:0;top:0}
.mini-card{position:absolute;left:350px;top:245px;width:110px;height:62px;background:var(--paper);border-bottom:3px solid var(--ink);box-shadow:0 2px 4px rgba(0,0,0,.4)}
.mini-card .mark{position:absolute;left:3px;top:16px;width:46px}
.mini-card .mark-square{width:10px;height:10px}
.mini-card .mark-name{font-size:5.4px}
.mini-card .divider{position:absolute;left:51px;top:10px;width:.6px;height:40px;background:var(--ink)}
.mini-card .details{position:absolute;left:55px;top:10px;font-size:3.4px;line-height:1.35}
.mini-card .person-name{font-size:5px}

/* small card */
.card-small{left:924px;top:857px;width:218px;height:85px}
.card-small .band{height:6px}
.card-small .mark{position:absolute;left:18px;top:18px;width:84px}
.card-small .mark-square{width:18px;height:18px}
.card-small .mark-name{font-size:9.5px}
.card-small .divider{position:absolute;left:106px;top:18px;width:1px;height:50px;background:var(--ink)}
.card-small .details{position:absolute;left:113px;top:18px;font-size:4.8px;line-height:1.35}
.card-small .person-name{font-size:7px}
.card-small .person-role{margin-bottom:5px}
.card-small .social{position:absolute;right:6px;bottom:12px;display:flex;gap:2px}
.card-small .social i{display:block;width:7px;height:7px;border-radius:50%}
</style>
</head>
<body>

<!-- business card front -->
<section class="piece card-front">
  <div class="mark"><div class="mark-square"></div><div class="mark-name">HARLOW LAW</div></div>
  <div class="divider"></div>
  <div class="details">
    <div class="person-name">DORIAN VALE</div>
    <div class="person-role">Founder &amp; CEO</div>
    <div class="contact addr">48 Elm Row, Suite 5<br>Fairhaven, MA 02719</div>
    <div class="contact">
      <div><svg class="ico" width="7" height="7" viewBox="0 0 10 10"><path d="M2 1l2 2-1 1.5c.7 1.2 1.3 1.8 2.5 2.5L7 6l2 2-1.5 1.5C5 9 1 5 .5 1.5z" fill="#f7a01e"/></svg>(555) 014-2290</div>
      <div><svg class="ico" width="8" height="6" viewBox="0 0 10 7"><rect x=".5" y=".5" width="9" height="6" fill="none" stroke="#f7a01e"/><path d="M.5.5l4.5 3.5L9.5.5" fill="none" stroke="#f7a01e"/></svg>info@harlowlawllc.com</div>
      <div><svg class="ico" width="7" height="7" viewBox="0 0 10 10"><circle cx="5" cy="5" r="4.3" fill="none" stroke="#f7a01e"/><path d="M.7 5h8.6M5 .7c-2.5 2.6-2.5 6 0 8.6M5 .7c2.5 2.6 2.5 6 0 8.6" fill="none" stroke="#f7a01e" stroke-width=".8"/></svg>www.harlowlawllc.com</div>
    </div>
  </div>
  <div class="band"></div>
</section>

<!-- business card back -->
<section class="piece card-back" role="img" aria-label="Dark embossed repeating pattern on the card back"></section>

<!-- letterhead -->
<section class="piece letter">
  <div class="mark"><div class="mark-square"></div><div class="mark-name">HARLOW LAW</div></div>
  <div class="contact head-contact">48 Elm Row, Suite 5<br>Fairhaven, MA 02719<br><span style="color:var(--orange)">●</span> (555) 014-2290<br><span style="color:var(--orange)">●</span> info@harlowlawllc.com<br><span style="color:var(--orange)">●</span> www.harlowlawllc.com</div>
  <div class="body">
    <p>Dear customer,</p>
    <p>Lorem ipsum dolor sit amet, consectetur adipiscing elit, sed do eiusmod tempor incididunt ut labore et dolore magna aliqua. Ut enim ad minim veniam, quis nostrud exercitation ullamco laboris nisi ut aliquip ex ea commodo consequat. Duis aute irure dolor in reprehenderit in voluptate velit esse cillum dolore eu fugiat nulla pariatur. Excepteur sint occaecat cupidatat non proident, sunt in culpa qui officia deserunt mollit anim id est laborum.</p>
    <p>Lorem ipsum dolor sit amet, consectetur adipiscing elit, sed do eiusmod tempor incididunt ut labore et dolore magna aliqua. Ut enim ad minim veniam, quis nostrud exercitation ullamco laboris nisi ut aliquip ex ea commodo consequat. Duis aute irure dolor in reprehenderit in voluptate velit esse cillum dolore eu fugiat nulla pariatur. Excepteur sint occaecat cupidatat non proident, sunt in culpa qui officia deserunt mollit anim id est laborum.</p>
    <p>Lorem ipsum dolor sit amet, consectetur adipiscing elit, sed do eiusmod tempor incididunt ut labore et dolore magna aliqua. Ut enim ad minim veniam, quis nostrud exercitation ullamco laboris nisi ut aliquip ex ea commodo consequat. Duis aute irure dolor in reprehenderit in voluptate velit esse cillum dolore eu fugiat nulla pariatur. Excepteur sint occaecat cupidatat non proident, sunt in culpa qui officia deserunt mollit anim id est laborum.</p>
    <p>Lorem ipsum dolor sit amet, consectetur adipiscing elit, sed do eiusmod tempor incididunt ut labore et dolore magna aliqua. Ut enim ad minim veniam, quis nostrud exercitation ullamco laboris nisi ut aliquip ex ea commodo consequat. Duis aute irure dolor in reprehenderit.</p>
    <p>Yours Sincerely,</p>
  </div>
  <div class="sign">Ellis Marr<br>General Director
    <svg width="30" height="26" viewBox="0 0 30 26" role="img" aria-label="Handwritten signature"><path d="M3 6c4 0 6 6 4 12s-4 4-2 0 6-8 8-4-2 6 2 2 4-6 5-10 1 10 2 12" fill="none" stroke="#222" stroke-width=".8"/></svg>
  </div>
  <div class="band"></div>
</section>

<!-- envelope back -->
<section class="piece env-back">
  <div class="panel"></div>
  <div class="mark"><div class="mark-square"></div><div class="mark-name">HARLOW LAW</div></div>
  <div class="contact ret">48 Elm Row, Suite 5<br>Fairhaven, MA 02719</div>
  <div class="band"></div>
</section>

<!-- envelope flap side -->
<section class="piece env-front">
  <svg width="410" height="195" viewBox="0 0 410 195">
    <path d="M12 40 L10 192 L400 192 L398 40" fill="#fff" stroke="#c9c9cb" stroke-width="1"/>
    <path d="M0 0 H410 L395 40 Q385 48 370 50 L210 72 Q205 73 200 72 L40 50 Q25 48 15 40 Z" fill="#1b1b1c"/>
  </svg>
  <div class="mark"><div class="mark-square"></div><div class="mark-name">HARLOW LAW</div></div>
</section>

<!-- folder cover -->
<section class="piece folder-cover">
  <div class="spine" role="img" aria-label="Dark cover with faint repeating pattern fading downward"></div>
  <div class="back-info">Harlow Law LLC<br>2210 Civic Plaza Dr. Suite D Millbrook, MI 48001<br><span style="color:var(--orange)">●</span> (555) 017-4408 <span style="color:var(--orange)">●</span> info@harlowlawllc.com<br>www.harlowlawllc.com</div>
  <div class="mark"><div class="mark-square"></div><div class="mark-name">HARLOW LAW</div></div>
  <div class="web">www.<span>harlowlawllc</span>.com</div>
</section>

<!-- folder inside -->
<section class="piece folder-in">
  <div class="left"></div>
  <div class="sheet">
    <div class="mark"><div class="mark-square"></div><div class="mark-name">HARLOW LAW</div></div>
    <div class="contact head-contact">48 Elm Row, Suite 5<br>Fairhaven, MA 02719<br><span style="color:var(--orange)">●</span> (555) 014-2290<br><span style="color:var(--orange)">●</span> info@harlowlawllc.com<br><span style="color:var(--orange)">●</span> www.harlowlawllc.com</div>
    <div class="body">
      <p>Dear customer,</p>
      <p>Lorem ipsum dolor sit amet, consectetur adipiscing elit, sed do eiusmod tempor incididunt ut labore et dolore magna aliqua. Ut enim ad minim veniam, quis nostrud exercitation ullamco laboris nisi ut aliquip ex ea commodo consequat.</p>
      <p>Lorem ipsum dolor sit amet, consectetur adipiscing elit, sed do eiusmod tempor incididunt ut labore et dolore magna aliqua. Ut enim ad minim veniam, quis nostrud exercitation ullamco laboris nisi ut aliquip ex ea commodo consequat.</p>
      <p>Lorem ipsum dolor sit amet, consectetur adipiscing elit, sed do eiusmod tempor incididunt ut labore et dolore magna aliqua. Ut enim ad minim veniam, quis nostrud exercitation ullamco laboris.</p>
    </div>
  </div>
  <svg class="pocket" width="531" height="346" viewBox="0 0 531 346">
    <path d="M0 223 H252 L265 346 H0 Z" fill="#1b1b1c"/>
    <path d="M278 223 H531 V346 H265 Z" fill="#1b1b1c"/>
  </svg>
  <div class="mini-card">
    <div class="mark"><div class="mark-square"></div><div class="mark-name">HARLOW LAW</div></div>
    <div class="divider"></div>
    <div class="details contact">
      <div class="person-name">DORIAN VALE</div>
      <div class="person-role">Founder &amp; CEO</div>
      48 Elm Row, Suite 5<br>Fairhaven, MA 02719<br>(555) 014-2290<br>info@harlowlawllc.com<br>www.harlowlawllc.com
    </div>
  </div>
</section>

<!-- small business card -->
<section class="piece card-small">
  <div class="mark"><div class="mark-square"></div><div class="mark-name">HARLOW LAW</div></div>
  <div class="divider"></div>
  <div class="details contact">
    <div class="person-name">DORIAN VALE</div>
    <div class="person-role">Founder &amp; CEO</div>
    48 Elm Row, Suite 5<br>Fairhaven, MA 02719<br>
    <span style="color:var(--orange)">●</span> (555) 014-2290<br>
    <span style="color:var(--orange)">●</span> info@harlowlawllc.com<br>
    <span style="color:var(--orange)">●</span> www.harlowlawllc.com
  </div>
  <div class="social"><i style="background:#3b5b98"></i><i style="background:#2aa3ef"></i><i style="background:#4caf50"></i></div>
  <div class="band"></div>
</section>

</body>
</html>
```